Australian Trucking Company Requires Professional Looking Stationary

We require a professional looking stationary design that incorporates our newly designed logo.

Our business, called "Brell Haulage Contracting", provides contracting work, transport and logistics to business in Western Australia particularly with links to the mining sector.

We are a small business looking to expand and our new logo and our new stationary will help develop our brand image in our market place.

Target Market(s)

Businesses and Corporation with links to the Mining Sector

Industry/Entity Type

Small Business

Requirements
Must have
• The letterhead must have the following details:
The new logo

Text saying: "Brell Holdings Pty Ltd (ACN 582 316 907) ATF The Brell Discretionary Trust T/AS"
"ABN 71 834 209 553"
Address "P.O Box 817 Wattlegrove WA, 6958"
Phone: 08 9352 7140
Email: brellhaul@mailbox-example.com.au

The text on the letterhead should be editable as the details are likely to change in the near future. Provision should be made for a website address all though one isn't available at the moment.

The styling, layout and font text is entirely up to the designer.

```html
<!DOCTYPE html>
<html lang="en">
<head>
<meta charset="utf-8">
<title>Brell Haulage Contracting – Business Cards</title>
<link href="https://fonts.googleapis.com/css2?family=Arimo:wght@400;700&display=swap" rel="stylesheet">
<style>
  :root {
    --bg: #e9e6e2;
    --card-white: #ffffff;
    --brand-red: #8e1a1f;
    --brand-red-bright: #b3202a;
    --silver-light: #f2f2f2;
    --silver-dark: #8a8a8a;
    --grey-text: #a9a9a9;
    --logo-grey: #6f6f6f;
    --on-red: #ffffff;
  }
  * { box-sizing: border-box; margin: 0; padding: 0; }
  html, body {
    width: 1200px; height: 665px; overflow: hidden;
    background: var(--bg);
    font-family: "Arimo", Arial, sans-serif;
  }
  .canvas { position: relative; width: 1200px; height: 665px; }

  .card {
    position: absolute; top: 178px;
    width: 540px; height: 310px;
    border-radius: 24px; overflow: hidden;
    background: var(--card-white);
    box-shadow: 0 6px 18px rgba(0,0,0,0.18);
  }
  .card--front { left: 40px; }
  .card--back { left: 620px; }
  .card__shape { position: absolute; inset: 0; }

  .brand { position: absolute; display: flex; align-items: center; gap: 16px; }
  .brand__square {
    width: 80px; height: 80px; border-radius: 6px;
    background: var(--logo-grey);
  }
  .brand__name {
    color: var(--brand-red-bright);
    font-weight: 700; font-size: 28px; line-height: 1.02;
    text-transform: uppercase; letter-spacing: 0.5px;
  }
  .card--front .brand { left: 56px; top: 22px; }
  .card--back .brand { left: 70px; top: 56px; }
  .card--back .brand__square { width: 104px; height: 104px; }
  .card--back .brand__name { font-size: 36px; }

  .abn {
    position: absolute; left: 168px; top: 124px;
    color: var(--grey-text); font-size: 12px; letter-spacing: 0.3px;
  }
  .person {
    position: absolute; left: 168px; top: 142px;
    color: var(--brand-red); font-size: 15px; font-weight: 700;
    white-space: nowrap;
  }
  .person__title { font-weight: 400; font-size: 12px; margin-left: 4px; }

  .contact {
    position: absolute; left: 0; right: 0; bottom: 18px;
    color: var(--on-red); font-size: 11px; text-align: center; line-height: 1.9;
  }
  .contact__row { display: flex; justify-content: center; gap: 16px; }
  .contact__item { display: inline-flex; align-items: center; gap: 5px; }
  .contact__icon { width: 10px; height: 10px; fill: var(--on-red); }

  .web {
    position: absolute; left: 0; right: 0; bottom: 14px;
    text-align: center; color: var(--on-red); font-size: 13px; letter-spacing: 0.4px;
  }
  .web strong { font-size: 15px; }
</style>
</head>
<body>
<main class="canvas">

  <section class="card card--front" aria-label="Business card front">
    <svg class="card__shape" viewBox="0 0 540 310" preserveAspectRatio="none" aria-hidden="true">
      <defs>
        <linearGradient id="silver-front" x1="0" x2="1" y1="0" y2="0">
          <stop offset="0" stop-color="var(--silver-dark)"/>
          <stop offset="0.5" stop-color="var(--silver-light)"/>
          <stop offset="1" stop-color="var(--silver-dark)"/>
        </linearGradient>
      </defs>
      <path d="M0,212 Q250,200 540,130 L540,310 L0,310 Z" fill="url(#silver-front)"/>
      <path d="M0,222 Q250,210 540,140 L540,310 L0,310 Z" fill="var(--brand-red)"/>
    </svg>

    <div class="brand">
      <span class="brand__square"></span>
      <span class="brand__name">Brell<br>Haulage<br>Contracting</span>
    </div>
    <p class="abn">ABN 71 834 209 553</p>
    <p class="person">Name here &nbsp;/<span class="person__title">Title</span></p>

    <div class="contact">
      <p>P.O Box 817 Wattlegrove WA, 6958</p>
      <p class="contact__row">
        <span class="contact__item">
          <svg class="contact__icon" viewBox="0 0 10 10"><path d="M2,0.5 L3.6,2.6 L2.7,3.6 Q3.6,5.6 6.4,7.3 L7.4,6.4 L9.5,8 L8.3,9.5 Q1,8 0.5,1.7 Z"/></svg>
          08 9352 7140
        </span>
        <span class="contact__item">
          <svg class="contact__icon" viewBox="0 0 10 10"><path d="M0,2 L10,2 L10,8 L0,8 Z M0.6,2.4 L5,5.6 L9.4,2.4" stroke="var(--brand-red)" stroke-width="0.8"/></svg>
          brellhaul@mailbox-example.com.au
        </span>
        <span class="contact__item">
          <svg class="contact__icon" viewBox="0 0 10 10"><circle cx="5" cy="5" r="4.5"/><path d="M0.5,5 H9.5 M5,0.5 V9.5 M5,0.5 Q2,5 5,9.5 M5,0.5 Q8,5 5,9.5" stroke="var(--brand-red)" stroke-width="0.7" fill="none"/></svg>
          www.brellhaulage.com.au
        </span>
      </p>
      <p>Brell Holdings Pty Ltd (ACN 582 316 907) ATF The Brell Discretionary Trust T/AS</p>
    </div>
  </section>

  <section class="card card--back" aria-label="Business card back">
    <svg class="card__shape" viewBox="0 0 540 310" preserveAspectRatio="none" aria-hidden="true">
      <defs>
        <linearGradient id="silver-back" x1="0" x2="1" y1="0" y2="0">
          <stop offset="0" stop-color="var(--silver-dark)"/>
          <stop offset="0.5" stop-color="var(--silver-light)"/>
          <stop offset="1" stop-color="var(--silver-dark)"/>
        </linearGradient>
      </defs>
      <path d="M0,176 Q190,258 540,262 L540,310 L0,310 Z" fill="url(#silver-back)"/>
      <path d="M0,188 Q190,268 540,272 L540,310 L0,310 Z" fill="var(--brand-red)"/>
    </svg>

    <div class="brand">
      <span class="brand__square"></span>
      <span class="brand__name">Brell<br>Haulage<br>Contracting</span>
    </div>
    <p class="web">www.<strong>brellhaulage</strong>.com.au</p>
  </section>

</main>
</body>
</html>
```